Cafe - A FRAME Design

Need to create an A frame for my café.
Logo available
Word document - has basic information we think would be good.

Name: Wuzzop Café

Notes from the A-frame printers.
File Requirements
• PDF without trim, crop or registration marks
• All files to be CMYK, not RGB
• All fonts converted to outlines (paths/curves)
• Embed all images and elements
• Files to be 100% scale unless otherwise specified
• 10mm Bleed
Resolution
• Bitmap images no less than 130 DPI at full size
Pantone Colours
• If required Pantone colours must be supplied

Target Market(s)

Mainly Students - University cafe

Requirements
Must have
• Cafe name: Wuzzop
Nice to have
• Might be nice to have background - that orange color same as logo - just an idea

Word document - has basic idea regarding text that should be included

```html
<!DOCTYPE html>
<html lang="en">
<head>
<meta charset="utf-8">
<title>Wuzzop Café – A-Frame</title>
<link rel="stylesheet" href="https://fonts.googleapis.com/css2?family=Montserrat:wght@600;700;800&family=Yellowtail&family=Open+Sans:wght@400;700&display=swap">
<style>
  :root {
    --orange: #e8632c;
    --board: #161514;
    --white: #ffffff;
    --bean-dark: #2a160c;
    --bean-mid: #5a331c;
    --page: #ecebe8;
  }
  * { box-sizing: border-box; margin: 0; padding: 0; }
  html, body {
    width: 1054px; height: 1200px; overflow: hidden;
    background: var(--page);
  }
  .aframe {
    position: absolute; left: 197px; top: 20px;
    width: 660px; height: 1160px;
    background: var(--board);
    overflow: hidden;
    color: var(--white);
    font-family: "Montserrat", sans-serif;
    text-align: center;
  }
  .bean-header {
    position: absolute; left: 0; top: 0; width: 100%; height: 320px;
    background:
      radial-gradient(ellipse at 30% 25%, var(--bean-mid) 0%, transparent 55%),
      radial-gradient(ellipse at 75% 35%, var(--bean-mid) 0%, transparent 50%),
      linear-gradient(to bottom, var(--bean-dark) 0%, #24140b 60%, var(--board) 100%);
  }
  .brand {
    position: absolute; left: 0; top: 130px; width: 100%;
    display: flex; justify-content: center; align-items: center; gap: 18px;
  }
  .brand-dot {
    width: 26px; height: 26px; border-radius: 50%; background: var(--orange);
  }
  .brand-name {
    font-weight: 700; font-size: 68px; letter-spacing: -1px; color: var(--white);
  }
  .tagline {
    position: absolute; left: 0; top: 305px; width: 100%;
    font-weight: 800; font-size: 25px; line-height: 1.3; text-transform: uppercase;
  }
  .divider {
    position: absolute; left: 295px; top: 410px; width: 70px; height: 5px; background: var(--white);
  }
  .headline { font-weight: normal; }
  .headline-script {
    position: absolute; left: 0; top: 410px; width: 100%;
    font-family: "Yellowtail", cursive; font-size: 128px; line-height: 1;
    white-space: nowrap;
    color: var(--orange); z-index: 2;
  }
  .headline-main {
    position: absolute; left: 0; top: 560px; width: 100%;
    font-weight: 800; font-size: 146px; line-height: 1; letter-spacing: -3px;
    white-space: nowrap;
    z-index: 1;
  }
  .offer-list {
    position: absolute; left: 60px; top: 762px; width: 540px;
    display: flex; justify-content: space-between; list-style: none;
  }
  .offer {
    flex: 1; display: flex; flex-direction: column; align-items: center; gap: 14px;
    font-weight: 700; font-size: 23px; letter-spacing: -0.3px;
    text-transform: uppercase; white-space: nowrap;
  }
  .offer + .offer { border-left: 2px solid var(--orange); }
  .offer-icon {
    width: 76px; height: 76px; border: 2px solid var(--orange); border-radius: 50%;
    display: flex; align-items: center; justify-content: center;
  }
  .offer-icon svg { width: 46px; height: 46px; fill: none; stroke: var(--white); stroke-width: 2.2; stroke-linejoin: round; stroke-linecap: round; }
  .notice-band {
    position: absolute; left: 68px; top: 912px; width: 538px; height: 94px;
    background: var(--orange);
    display: flex; flex-direction: column; justify-content: center;
    font-family: "Open Sans", sans-serif; font-size: 26px; line-height: 1.2;
  }
  .notice-band strong { font-family: "Montserrat", sans-serif; font-weight: 700; }
  .location {
    position: absolute; left: 0; top: 1062px; width: 100%;
    display: flex; justify-content: center; align-items: center; gap: 14px;
    font-weight: 700; font-size: 26px; text-transform: uppercase;
  }
  .location svg { width: 26px; height: 36px; }
</style>
</head>
<body>
<main class="aframe">
  <div class="bean-header" role="img" aria-label="Close-up photograph of roasted coffee beans fading into black"></div>

  <div class="brand">
    <span class="brand-dot"></span>
    <span class="brand-name">Wuzzop</span>
  </div>

  <p class="tagline">Your environmentally &amp;<br>sustainability focused café</p>
  <div class="divider"></div>

  <h1 class="headline">
    <span class="headline-script">Specialty</span>
    <span class="headline-main">Coffee</span>
  </h1>

  <ul class="offer-list">
    <li class="offer">
      <span class="offer-icon">
        <svg viewBox="0 0 48 48"><path d="M8 22a16 10 0 0 1 32 0z"/><path d="M7 27h34"/><path d="M9 32h30v5H9z"/></svg>
      </span>
      Fresh Food
    </li>
    <li class="offer">
      <span class="offer-icon">
        <svg viewBox="0 0 48 48"><path d="M10 24c0-9 6-14 14-14s14 5 14 14z"/><path d="M11 24l4 16h18l4-16"/><path d="M20 24l1 16M28 24l-1 16"/></svg>
      </span>
      Pastries
    </li>
    <li class="offer">
      <span class="offer-icon">
        <svg viewBox="0 0 48 48"><path d="M13 14h22l-3 28H16z"/><path d="M11 14h26"/><path d="M25 14l2-10h4"/><circle cx="21" cy="28" r="2"/><circle cx="27" cy="34" r="2"/></svg>
      </span>
      Drinks
    </li>
  </ul>

  <div class="notice-band">
    <span>(VEGAN &amp; GF) OPTIONS AVAILABLE</span>
    <strong>CATERING AVAILABLE</strong>
  </div>

  <p class="location">
    <svg viewBox="0 0 26 36"><path d="M13 1C6.4 1 1 6.2 1 12.8 1 22 13 35 13 35s12-13 12-22.2C25 6.2 19.6 1 13 1z" fill="var(--orange)"/><circle cx="13" cy="12.5" r="4.5" fill="var(--board)"/></svg>
    Located @ Building 317
  </p>
</main>
</body>
</html>
```